Stationery & Envelope Design

Executive Style looking stationery & envelope design.
Business Information:
Larkspur Home Group
2875 Birchwood Lane, Fairbrook, CA 95661-4180
Phone: 916.555.0142
Fax: 916.555.0187

Industry/Entity Type

Business

```html
<!DOCTYPE html>
<html lang="en">
<head>
<meta charset="utf-8">
<title>Larkspur Home Group Stationery Set</title>
<link rel="stylesheet" href="https://fonts.googleapis.com/css2?family=Arimo:wght@400;700&display=swap">
<style>
:root{
  --stage:#dcd7cf;
  --paper:#ffffff;
  --navy:#1d4f94;
  --olive:#7a8a3a;
  --ink:#222222;
  --rule:#2b2b2b;
  --edge:#b9b5ae;
  --muted-white:rgba(255,255,255,.45);
}
*{box-sizing:border-box;margin:0;padding:0}
html,body{width:1200px;height:1089px;overflow:hidden}
body{background:var(--stage);font-family:"Arimo",Arial,sans-serif;color:var(--ink);position:relative}
.sheet,.envelope{position:absolute;background:var(--paper);border:1px solid var(--edge);overflow:hidden}
.sheet{top:36px;width:470px;height:612px}
.sheet--fax{left:85px}
.sheet--letter{left:640px}
.header-band{position:absolute;top:0;left:0;width:100%;height:130px}
.company-mark{position:absolute;font-weight:700;color:var(--navy);display:flex;align-items:center;gap:6px;white-space:nowrap}
.company-mark .dot{width:9px;height:9px;background:var(--olive)}
.sheet .company-mark{left:33px;top:86px;font-size:15px}
.tagline{position:absolute;font-size:6px;color:var(--ink)}
.sheet .tagline{left:48px;top:106px}
.return-address{position:absolute;right:18px;top:10px;color:#fff;font-size:8px;line-height:11px}
.return-address strong{display:block;font-size:9.5px;margin-bottom:2px}
.top-contacts{position:absolute;left:33px;top:6px;color:#fff;font-size:7.5px;display:flex;gap:10px}
.top-contacts span{display:flex;align-items:center;gap:3px}
.fax-title{position:absolute;left:33px;top:118px;font-size:30px;font-weight:400}
.fax-field{position:absolute;font-size:11px;border-bottom:1.5px solid var(--rule);padding-bottom:9px}
.fax-field--left{left:39px;width:239px}
.fax-field--right{left:292px;width:138px}
.fax-footer{position:absolute;bottom:8px;left:0;width:100%;text-align:center;font-size:8px}
.fax-footer b{font-weight:700}
.envelope svg.flap{position:absolute;top:0;left:0;width:100%;height:72px}
.flap-mark{position:absolute;top:24px;left:0;width:100%;display:flex;justify-content:center;font-weight:700;font-size:15px}
.envelope--back1{left:80px;top:675px;width:527px;height:229px}
.envelope--back2{left:51px;top:745px;width:526px;height:230px}
.envelope--front{left:36px;top:822px;width:528px;height:229px}
.envelope--front .company-mark{left:17px;top:78px;font-size:12px}
.envelope--front .tagline{left:30px;top:94px;font-size:5px}
.envelope--front .header-band{height:100px}
.envelope--front .sender-line{position:absolute;left:17px;top:103px;font-size:8px}
.envelope--green{left:624px;top:666px;width:527px;height:298px}
.envelope--blue{left:608px;top:736px;width:527px;height:300px}
.envelope--white{left:642px;top:817px;width:528px;height:228px}
.ghost-name{position:absolute;right:30px;top:20px;font-weight:700;font-size:13px;color:var(--muted-white)}
</style>
</head>
<body>

<svg width="0" height="0" style="position:absolute"><defs><linearGradient id="bandA" x1="0" y1="0" x2="0" y2="1"><stop offset="0" stop-color="#2460a8"/><stop offset="1" stop-color="#163a74"/></linearGradient></defs></svg>

<section class="sheet sheet--fax" aria-label="Fax cover sheet">
  <svg class="header-band" viewBox="0 0 470 130" preserveAspectRatio="none">
    <path d="M0 0H470V92C360 40 180 30 0 52Z" fill="url(#bandA)"/>
    <path d="M0 86C70 62 180 50 240 52C170 56 70 70 0 100Z" fill="#7a8a3a"/>
  </svg>
  <div class="return-address"><strong>Larkspur Home Group</strong>2875 Birchwood Lane<br>Fairbrook, CA 95661-4180</div>
  <div class="company-mark"><span class="dot"></span>Larkspur Home Group</div>
  <p class="tagline">A fresh start in every home</p>
  <h1 class="fax-title">FAX</h1>
  <div class="fax-field fax-field--left" style="top:194px">To</div>
  <div class="fax-field fax-field--right" style="top:194px">From</div>
  <div class="fax-field fax-field--left" style="top:248px">Fax</div>
  <div class="fax-field fax-field--right" style="top:248px">Pages</div>
  <div class="fax-field fax-field--left" style="top:302px">Phone</div>
  <div class="fax-field fax-field--right" style="top:302px">Date</div>
  <div class="fax-field fax-field--left" style="top:358px">Re</div>
  <div class="fax-field fax-field--right" style="top:358px">CC</div>
  <p class="fax-footer"><b>P</b>: 916.555.0142 | <b>F</b>: 916.555.0187</p>
</section>

<section class="sheet sheet--letter" aria-label="Letterhead">
  <svg class="header-band" viewBox="0 0 470 130" preserveAspectRatio="none">
    <path d="M0 0H470V92C360 40 180 30 0 52Z" fill="url(#bandA)"/>
    <path d="M0 86C70 62 180 50 240 52C170 56 70 70 0 100Z" fill="#7a8a3a"/>
  </svg>
  <div class="top-contacts">
    <span><svg width="7" height="7" viewBox="0 0 10 10"><path d="M2 0L4 3 3 4Q4 6 6 7L7 6 10 8 8 10Q0 9 0 2Z" fill="#fff"/></svg>916.555.0142</span>
    <span><svg width="8" height="7" viewBox="0 0 10 9"><rect x="1" y="3" width="8" height="6" fill="#fff"/><rect x="3" y="0" width="4" height="3" fill="#fff"/></svg>916.555.0187</span>
  </div>
  <div class="return-address"><strong>Larkspur Home Group</strong>2875 Birchwood Lane<br>Fairbrook, CA 95661-4180</div>
  <div class="ghost-name" style="top:52px;font-size:11px">Larkspur</div>
  <div class="company-mark"><span class="dot"></span>Larkspur Home Group</div>
  <p class="tagline">A fresh start in every home</p>
</section>

<section class="envelope envelope--back1" aria-label="Envelope back, colour mark">
  <svg class="flap" viewBox="0 0 527 72" preserveAspectRatio="none"><polyline points="0,0 14,68 513,68 527,0" fill="none" stroke="#bbb"/></svg>
  <div class="flap-mark" style="color:var(--navy)">Larkspur Home Group</div>
</section>

<section class="envelope envelope--back2" aria-label="Envelope back, grey mark">
  <svg class="flap" viewBox="0 0 526 72" preserveAspectRatio="none"><polyline points="0,0 14,66 512,66 526,0" fill="none" stroke="#bbb"/></svg>
  <div class="flap-mark" style="color:#555">Larkspur Home Group</div>
</section>

<section class="envelope envelope--front" aria-label="Envelope front">
  <svg class="header-band" viewBox="0 0 528 100" preserveAspectRatio="none">
    <path d="M0 0H528V72C400 30 200 22 0 40Z" fill="url(#bandA)"/>
    <path d="M0 66C80 46 200 36 275 38C195 42 80 54 0 78Z" fill="#7a8a3a"/>
  </svg>
  <div class="ghost-name">Larkspur</div>
  <div class="company-mark"><span class="dot"></span>Larkspur Home Group</div>
  <p class="tagline">A fresh start in every home</p>
  <p class="sender-line">Larkspur Home Group, 2875 Birchwood Lane, Fairbrook, CA 95661-4180</p>
</section>

<section class="envelope envelope--green" aria-label="Envelope with olive flap">
  <svg class="flap" viewBox="0 0 527 72" preserveAspectRatio="none"><polygon points="0,0 527,0 512,72 15,72" fill="#7a8a3a"/></svg>
  <div class="flap-mark" style="color:#fff">Larkspur Home Group</div>
</section>

<section class="envelope envelope--blue" aria-label="Envelope with navy flap">
  <svg class="flap" viewBox="0 0 527 72" preserveAspectRatio="none"><polygon points="0,0 527,0 512,72 15,72" fill="url(#bandA)"/></svg>
  <div class="flap-mark" style="color:#fff">Larkspur Home Group</div>
</section>

<section class="envelope envelope--white" aria-label="Envelope with black mark">
  <svg class="flap" viewBox="0 0 528 72" preserveAspectRatio="none"><polyline points="0,0 14,66 514,66 528,0" fill="none" stroke="#bbb"/></svg>
  <div class="flap-mark" style="color:#111">Larkspur Home Group</div>
</section>

</body>
</html>
```